Business card design needed

OH&S consultancy and training

Industry/Entity Type

Training

Contact Information for Business Card

Coastal Hazard & Learning Collective
Dorian Whitfield
Director

0427 913 058
dorian.whitfield@chlcollect.com.au
chlcollect.com.au

Ph: 03 9172 4039
Fx: 03 9172 4041

```html
<!DOCTYPE html>
<html lang="en">
<head>
<meta charset="utf-8">
<title>Coastal Hazard &amp; Learning Collective – Business Card</title>
<link rel="stylesheet" href="https://fonts.googleapis.com/css2?family=Barlow:wght@400;500;600&display=swap">
<style>
  :root {
    --navy: #0f3044;
    --navy-deep: #0b2535;
    --yellow: #f2e600;
    --ink: #2b2b2b;
    --logo-grey: #b9bcbf;
    --paper: #ffffff;
    --backdrop: #d9dee1;
  }
  * { box-sizing: border-box; margin: 0; padding: 0; }
  html, body {
    width: 1200px; height: 960px; overflow: hidden;
    background: var(--backdrop);
    font-family: "Barlow", Arial, sans-serif;
  }
  .canvas {
    width: 1200px; height: 960px;
    display: flex; flex-direction: column;
    align-items: center; justify-content: center; gap: 60px;
  }
  .card {
    width: 560px; height: 342px;
    position: relative; overflow: hidden;
    box-shadow: 0 6px 18px rgba(0,0,0,.18);
  }

  /* Front: contact side */
  .card--front { background: var(--paper); display: flex; }
  .front-brand {
    width: 200px; height: 100%;
    background: var(--navy);
    border-right: 5px solid var(--yellow);
    position: relative;
  }
  .front-brand .brand-mark {
    position: absolute; left: 50%; top: 50%;
    transform: translate(-50%, -50%) rotate(-90deg);
    display: flex; align-items: center; gap: 12px;
    white-space: nowrap;
  }
  .brand-square { width: 22px; height: 22px; background: var(--yellow); flex: none; }
  .brand-name {
    color: var(--logo-grey); font-weight: 500;
    line-height: 1.1;
  }
  .front-brand .brand-name { font-size: 17px; }

  .front-details { flex: 1; padding: 42px 30px 0 40px; color: var(--ink); }
  .person-name { font-size: 28px; font-weight: 400; letter-spacing: .3px; }
  .person-role { font-size: 16px; margin-top: 6px; }
  .rule { height: 2px; background: var(--yellow); margin: 18px 0 16px; }
  .phones { list-style: none; font-size: 16px; line-height: 1.45; }
  .phones li { display: flex; gap: 14px; }
  .phones .label { color: #e0d300; width: 12px; }
  .web-lines { font-size: 15px; line-height: 1.6; }
  .web-lines .site { font-weight: 600; font-size: 16px; }

  /* Back: brand side */
  .card--back {
    background: linear-gradient(135deg, var(--navy) 0%, var(--navy-deep) 100%);
    display: flex; align-items: center; justify-content: center;
  }
  .card--back .brand-mark { display: flex; align-items: center; gap: 16px; }
  .card--back .brand-square { width: 34px; height: 34px; }
  .card--back .brand-name { font-size: 27px; }
</style>
</head>
<body>
<main class="canvas">
  <section class="card card--front" aria-label="Business card front">
    <div class="front-brand">
      <div class="brand-mark">
        <span class="brand-square"></span>
        <span class="brand-name">Coastal Hazard &amp; Learning Collective</span>
      </div>
    </div>
    <div class="front-details">
      <h1 class="person-name">Dorian Whitfield</h1>
      <p class="person-role">Director</p>
      <div class="rule"></div>
      <ul class="phones">
        <li><span class="label">M</span><span>0427 913 058</span></li>
        <li><span class="label">T</span><span>03 9172 4039</span></li>
        <li><span class="label">F</span><span>03 9172 4041</span></li>
      </ul>
      <div class="rule"></div>
      <p class="web-lines">dorian.whitfield@chlcollect.com.au<br><span class="site">chlcollect.com.au</span></p>
    </div>
  </section>

  <section class="card card--back" aria-label="Business card back">
    <div class="brand-mark">
      <span class="brand-square"></span>
      <span class="brand-name">Coastal Hazard &amp; Learning Collective</span>
    </div>
  </section>
</main>
</body>
</html>
```